Quillmere Supply Chain and Logistic Consulting

Please review the attached Business Card. I want as close to this card with the colors, fonts, and quality of the card as possible. The attached compass should replace the deer head on both sides of the card and the text should say:

Backside
Compass JPEG
Quillmere SC&L
A Supply Chain and Logistics Consulting Company

Frontside
Quillmere SC&L
Ray Falkner - Tampa Florida
President
____________________________________
(555) 314-9027
QuillmereSCL@Examplemail.com
_____________________________________

Bottom Front Side

Target Market(s)

Businesses

Contact Information for Business Card

Backside
Compass JPEG
Quillmere SC&L

Frontside
Quillmere SC&L
President
(555) 314-9027
QuillmereSCL@Examplemail.com

Bottom Front Side

Font styles to use
Serif
Script

Colors

Designer to choose colors to be used in the design.

Requirements
Must have
• See attached card for reference
Nice to have
Should not have

```html
<!DOCTYPE html>
<html lang="en">
<head>
<meta charset="utf-8">
<title>Quillmere SC&amp;L – Business Card</title>
<link rel="stylesheet" href="https://fonts.googleapis.com/css2?family=Marcellus&family=Marcellus+SC&family=Tinos:wght@400;700&display=swap">
<style>
  :root {
    --backdrop: #2b2b2d;
    --card-top: #161616;
    --card-bottom: #050505;
    --ink-silver: #d9d9d9;
    --ink-soft: #bdbdbd;
    --rule: #5a5a5a;
    --metal-dark: #6f6f6f;
    --metal-light: #f4f4f4;
  }
  * { box-sizing: border-box; margin: 0; padding: 0; }
  html, body { width: 1200px; height: 900px; overflow: hidden; }
  body {
    background: var(--backdrop);
    display: flex;
    flex-direction: column;
    align-items: center;
    justify-content: center;
    gap: 44px;
  }
  .card {
    position: relative;
    width: 620px;
    height: 354px;
    background: linear-gradient(160deg, var(--card-top), var(--card-bottom));
    border-radius: 3px;
    color: var(--ink-silver);
    display: flex;
    flex-direction: column;
    align-items: center;
    overflow: hidden;
  }
  .card::after {
    content: "";
    position: absolute;
    left: 0; right: 0; bottom: 14px;
    height: 9px;
    background: linear-gradient(90deg, var(--metal-dark), var(--metal-light) 30%, var(--metal-dark) 55%, var(--metal-light) 80%, var(--metal-dark));
  }
  .brand-name {
    font-family: "Marcellus", serif;
    font-size: 40px;
    letter-spacing: 2px;
    color: var(--ink-silver);
  }

  /* back side */
  .card--back { justify-content: center; padding-bottom: 30px; }
  .brand-mark {
    width: 150px; height: 150px;
    border-radius: 50%;
    border: 2px solid var(--ink-silver);
    margin-bottom: 14px;
  }
  .card--back .brand-name { font-size: 34px; }

  /* front side */
  .card--front { padding-top: 34px; }
  .holder {
    margin-top: 14px;
    font-family: "Tinos", serif;
    font-weight: 700;
    font-size: 25px;
    color: #ececec;
  }
  .role {
    font-family: "Tinos", serif;
    font-size: 17px;
    color: var(--ink-soft);
  }
  .rule {
    width: 290px;
    height: 1px;
    background: linear-gradient(90deg, transparent, var(--rule), transparent);
    margin: 8px 0;
  }
  .contact {
    font-family: "Tinos", serif;
    font-size: 18px;
    line-height: 1.3;
    text-align: center;
    color: #e4e4e4;
  }
  .tagline {
    position: absolute;
    bottom: 36px;
    font-family: "Marcellus SC", serif;
    font-size: 19px;
    letter-spacing: 1.5px;
    color: var(--ink-soft);
  }
</style>
</head>
<body>
  <section class="card card--back" aria-label="Card back">
    <div class="brand-mark"></div>
    <div class="brand-name">QUILLMERE SC&amp;L</div>
  </section>

  <section class="card card--front" aria-label="Card front">
    <div class="brand-name">QUILLMERE SC&amp;L</div>
    <div class="holder">Ray Falkner - Tampa Florida</div>
    <div class="role">President</div>
    <div class="rule"></div>
    <div class="contact">
      <div>(555) 314-9027</div>
      <div>QuillmereSCL@Examplemail.com</div>
    </div>
    <div class="rule"></div>
    <div class="tagline">A Supply Chain and Logistics Consulting Company</div>
  </section>
</body>
</html>
```